Venture Capital firm needs modern business cards

We are a Venture Capital firm within financial services/Asset management. The industry generally has basic business cards with black, blue and maybe green/yellow design elements.
Our firm has a four-colour swoosh logo. We are based in London and want to stand out, just a little bit!, from the crowd. Our company is called LORV Investments and the 'C' stands for collaboration thus using makerswarm is a natural portal for our business card design competition. Our logo came via makerswarm too!
We use 'Venture Partner in Asset Management' as our tagline and this is Trademark registered. We operate in a conservative industry and we should not overstep our mark. The logo is colorful as it is and therefore the rest of the design should not be too fanciful.
The objective is twofold: make our logo element stick and memorable with our audience, whilst representing a conservative yet young image.
Updates
The Business Card obviously needs a field for Name, Surname, Job Title, Adress fields: Street, City, Postcode, Country, telefone and cell number, website address, etc.
We have uploaded the ai file. We trust that these are OK. If not, please advise.
Reason: We have have been busy with a client engagement. We will set the project as Guaranteed in return for the troubles we cause. Apologies for the confusion.
Thank you all for these great and creative design suggestions. The team is very happy with a number of your ideas! We will be in touch tomorrow to give individual feedback before the project closes on Friday. We look forward to working with some of you to narrow down your creations. Thank you, LORV Investments team.
All,
Target Market(s)
Financial Services Professionals, Investors, Media, 35-70 years, mainly male, well educated
Industry/Entity Type
Conservative
Requirements
Must have
- We must make use of our logo and potential tagline 'Venture Partner in Asset Management' as we are establishing a new Brand and new company in the market.
We can use 'LORV', 'LORV Investments', and 'LORV Investments'+tagline 'Venture Partner in Asset Management' or simply the four-colour swoosh plus the name of the company as part of the text. (see files)
All design elements are available in black or grey-scale if required. (grey scale swoosh attached).
Due to regulation we must have the following wording on the card in small print 'LORV Investments is an Appointed Representative of Bramwell Holdings Partnership Limited, which is authorised by the Monetary Oversight Board'.
Nice to have
- We would consider designs that make use of different printing techniques such embossing/debossing, UV spot etc.
We attach our colour palette in the files section for your reference.
Should not have
- The font we use for our company name is 'EXO' so do not use a font style that clashes with the corporate fonts, please.
Do not use other design elements than the ones we provide in the file library as part of this project.

```html
<!DOCTYPE html>
<html lang="en">
<head>
<meta charset="utf-8">
<title>LORV Investments – Business Card Options</title>
<link href="https://fonts.googleapis.com/css2?family=Arimo:wght@400;700&family=Exo:wght@400&display=swap" rel="stylesheet">
<style>
  :root {
    --green: #5cb83c;
    --green-line: #a6da92;
    --card-grey: #c9c9c9;
    --band-grey: #c4c4c4;
    --mark-grey: #5a5a5a;
    --canvas: #e9e9e9;
    --white: #ffffff;
    --ink: #2b2b2b;
    --legal: #f4f4f4;
  }
  * { box-sizing: border-box; margin: 0; padding: 0; }
  html, body { width: 1200px; height: 556px; overflow: hidden; }
  body {
    position: relative;
    background: var(--white);
    font-family: "Arimo", Arial, sans-serif;
  }
  .presentation {
    position: absolute; left: 0; top: 0;
    width: 1200px; height: 510px;
    background: var(--canvas);
  }

  .card {
    position: absolute;
    width: 314px; height: 180px;
    overflow: hidden;
    box-shadow: 0 8px 10px -6px rgba(0,0,0,.35);
    transform-origin: 0 0;
  }
  .card--back { background: var(--card-grey); }
  .card--front { background: var(--white); }
  .card--large { transform: scale(1.2); }

  .brand-dot {
    position: absolute;
    border-radius: 50%;
  }
  .brand-dot--colour { background: var(--green); }
  .brand-dot--grey { background: var(--mark-grey); }

  .wordmark {
    font-family: "Exo", sans-serif;
    font-weight: 400;
    letter-spacing: 1px;
    line-height: 1;
  }

  /* back card */
  .address-block {
    position: absolute; left: 0; top: 88px;
    width: 191px; height: 64px;
    background: var(--green);
    color: var(--white);
    font-size: 9.5px;
  }
  .address-block .row {
    position: absolute; left: 0; right: 0;
    border-bottom: 1px solid var(--green-line);
  }
  .address-block .row--address { top: 0; height: 45px; }
  .address-block .row--web { top: 46px; height: 17px; border-bottom: 1px solid var(--green-line); }
  .row .key {
    position: absolute; left: 0; top: 0; bottom: 0;
    width: 11px;
    border-right: 1px solid var(--green-line);
    font-weight: 700; font-size: 8px;
    text-align: center; padding-top: 3px;
  }
  .row .value {
    position: absolute; left: 15px; top: 3px;
    line-height: 11px;
  }
  .row--web .value { top: 3px; }

  .logo-panel {
    position: absolute; left: 194px; top: 90px;
    width: 92px; height: 36px;
    background: var(--white);
    display: flex; align-items: center; justify-content: center;
  }
  .logo-panel .wordmark { color: var(--green); font-size: 22px; }

  .legal-note {
    position: absolute; left: 10px; top: 160px;
    width: 290px;
    color: var(--legal);
    font-size: 5.4px; line-height: 7px;
  }

  /* front card */
  .name-band {
    position: absolute; left: 0; top: 95px;
    width: 118px; height: 30px;
    background: var(--band-grey);
    display: flex; align-items: center; justify-content: center;
  }
  .name-band .wordmark { color: var(--white); font-size: 22px; }

  .contact-block {
    position: absolute; left: 122px; top: 91px;
    width: 193px; height: 64px;
    color: var(--white);
  }
  .contact-block .line {
    position: absolute; left: 0; right: 0;
    background: var(--green);
    font-size: 9px;
  }
  .line--person { top: 0; height: 20px; padding: 4px 0 0 4px; font-size: 10.5px; }
  .line--person strong { font-weight: 700; }
  .line--phones { top: 22px; height: 19px; }
  .line--email { top: 43px; height: 19px; }
  .contact-block .cell {
    position: absolute; top: 0; bottom: 0;
    padding-top: 4px;
  }
  .cell.key {
    width: 11px; text-align: center;
    font-weight: 700; font-size: 8px;
    border-right: 1px solid var(--green-line);
  }

  .note {
    position: absolute; left: 18px; top: 519px;
    font-size: 13px; color: var(--ink);
  }
</style>
</head>
<body>
<main class="presentation">

  <!-- colour option -->
  <section class="card card--front card--large" style="left:40px; top:50px;">
    <span class="brand-dot brand-dot--colour" style="left:12px; top:12px; width:54px; height:54px;"></span>
    <div class="name-band"><span class="wordmark">LORV</span></div>
    <div class="contact-block">
      <div class="line line--person"><strong>Martin Hale</strong> - Chairman</div>
      <div class="line line--phones">
        <span class="cell key" style="left:0;">M</span>
        <span class="cell" style="left:15px;">+1(800)555-0142</span>
        <span class="cell key" style="left:96px; border-left:1px solid var(--green-line);">M</span>
        <span class="cell" style="left:111px;">+1(800)555-0142</span>
      </div>
      <div class="line line--email">
        <span class="cell key" style="left:0;">E</span>
        <span class="cell" style="left:15px;">martin@lorvinvestments.com</span>
      </div>
    </div>
  </section>

  <section class="card card--back card--large" style="left:380px; top:250px;">
    <span class="brand-dot brand-dot--colour" style="left:247px; top:11px; width:52px; height:52px;"></span>
    <div class="address-block">
      <div class="row row--address">
        <span class="key">A</span>
        <span class="value">12 Harrow Lane,<br>7 Kestrel Square,<br>London, United Kingdom</span>
      </div>
      <div class="row row--web">
        <span class="key">W</span>
        <span class="value">www.lorvinvestments.com</span>
      </div>
    </div>
    <div class="logo-panel"><span class="wordmark">LORV</span></div>
    <p class="legal-note">'LORV Investments is an Appointed Representative of Bramwell Holdings Partnership Limited, which is authorised by the Monetary Oversight Board'</p>
  </section>

  <!-- grey option -->
  <section class="card card--back" style="left:836px; top:67px;">
    <span class="brand-dot brand-dot--grey" style="left:247px; top:11px; width:52px; height:52px;"></span>
    <div class="address-block">
      <div class="row row--address">
        <span class="key">A</span>
        <span class="value">12 Harrow Lane,<br>7 Kestrel Square,<br>London, United Kingdom</span>
      </div>
      <div class="row row--web">
        <span class="key">W</span>
        <span class="value">www.lorvinvestments.com</span>
      </div>
    </div>
    <div class="logo-panel"><span class="wordmark">LORV</span></div>
    <p class="legal-note">'LORV Investments is an Appointed Representative of Bramwell Holdings Partnership Limited, which is authorised by the Monetary Oversight Board'</p>
  </section>

  <section class="card card--front" style="left:840px; top:300px;">
    <span class="brand-dot brand-dot--grey" style="left:12px; top:12px; width:54px; height:54px;"></span>
    <div class="name-band"><span class="wordmark">LORV</span></div>
    <div class="contact-block">
      <div class="line line--person"><strong>Martin Hale</strong> - Chairman</div>
      <div class="line line--phones">
        <span class="cell key" style="left:0;">M</span>
        <span class="cell" style="left:15px;">+1(800)555-0142</span>
        <span class="cell key" style="left:96px; border-left:1px solid var(--green-line);">M</span>
        <span class="cell" style="left:111px;">+1(800)555-0142</span>
      </div>
      <div class="line line--email">
        <span class="cell key" style="left:0;">E</span>
        <span class="cell" style="left:15px;">martin@lorvinvestments.com</span>
      </div>
    </div>
  </section>

</main>
<p class="note">• Note : 1) Thes3 are 2 colour options, first one with the colourful swoosh and the second with grey.</p>
</body>
</html>
```